Business Card Design

We need a new business card design for a company based in Southlake, TX. We provide business consulting services in the information technology / services space. We like variations of the color blue, aqua, black, light tan, and white. Would like "cool" tones. The design should clearly communicate professionalism. Think outside the box - we don't want something "typical". Our company name is "Halvery Consulting, LLC".
Updates

Thank you all for your submissions. We have seen some very creative and inspired designs. We have made a decision and will be moving forward with that design. Appreciate all of the hard work.

Industry/Entity Type

Information Technology

Contact Information for Business Card

Megan Halvery Strube
218 West Birchfold Ridge Dr.
Southlake, TX 76418

```html
<!DOCTYPE html>
<html lang="en">
<head>
<meta charset="utf-8">
<title>Halvery Consulting, LLC — Business Card</title>
<link rel="stylesheet" href="https://fonts.googleapis.com/css2?family=Lora:wght@400;500&display=swap">
<style>
  :root {
    --backdrop: #e6e8eb;
    --card: #ffffff;
    --brand-blue: #1f4fa8;
    --ink: #1e1e1e;
    --shadow: rgba(20, 28, 40, 0.18);
  }
  * { margin: 0; padding: 0; box-sizing: border-box; }
  html, body {
    width: 1200px;
    height: 899px;
    overflow: hidden;
    background: var(--backdrop);
  }
  .stage {
    width: 1200px;
    height: 899px;
    display: flex;
    align-items: center;
    justify-content: center;
  }
  .business-card {
    position: relative;
    width: 840px;
    height: 480px;
    background: var(--card);
    box-shadow: 0 18px 40px var(--shadow);
    font-family: "Lora", Georgia, serif;
    color: var(--ink);
  }
  .accent-bar {
    position: absolute;
    left: 0;
    top: 168px;
    width: 56px;
    height: 62px;
    background: var(--brand-blue);
  }
  .contact-block {
    position: absolute;
    left: 82px;
    top: 160px;
  }
  .person-name {
    font-size: 40px;
    font-weight: 400;
    color: var(--brand-blue);
    letter-spacing: -0.3px;
    line-height: 1.1;
  }
  .address {
    margin-top: 26px;
    font-size: 21px;
    line-height: 1.3;
    font-style: normal;
  }
  .channels {
    margin-top: 54px;
    list-style: none;
    font-size: 21px;
    line-height: 1.35;
  }
  .channel-label {
    display: inline-block;
    width: 36px;
    color: var(--brand-blue);
  }
  .company-mark {
    position: absolute;
    right: 70px;
    top: 120px;
    display: flex;
    align-items: center;
    gap: 18px;
  }
  .company-square {
    width: 96px;
    height: 96px;
    border: 2px solid var(--brand-blue);
  }
  .company-name {
    font-size: 20px;
    font-weight: 400;
    color: var(--brand-blue);
    line-height: 1.3;
  }
</style>
</head>
<body>
  <main class="stage">
    <article class="business-card">
      <div class="company-mark">
        <div class="company-square"></div>
        <p class="company-name">Halvery<br>Consulting, LLC</p>
      </div>

      <div class="accent-bar"></div>

      <section class="contact-block">
        <h1 class="person-name">Megan Halvery Strube</h1>
        <address class="address">
          218 West Birchfold<br>
          Ridge Dr. Southlake, TX 76418
        </address>
        <ul class="channels">
          <li><span class="channel-label">E |</span>megan.strube@mailvane.com</li>
          <li><span class="channel-label">M |</span>713-555-0146</li>
        </ul>
      </section>
    </article>
  </main>
</body>
</html>
```